Banner ad series

We need a series of banner ads for 4 different digital products. The ads will drive traffic to these landing pages:
Relocate.set: http://pinnedtidygoods.example/relocatekit/
Treasures.file: http://pinnedtidygoods.example/digital-treasures-file/
Jumpstart Drill School: http://pinnedtidygoods.example/jumpstart-drill-school/
Vital Habits Drill School: http://pinnedtidygoods.example/vital-habits/

Banner Ad Sizes needed:
160x600, 728x90, 300x250

Text files with the copy/variations needed for each product are attached. In the text file - the first line of each option is the main headline. All other copy is support copy and OPTIONAL.

Target Market(s)

Our target market is a woman between the ages of 30-55 with kids. She's smart, working professionally and always on the lookout for products and services that will help her get more organized.

Industry/Entity Type

Digital

Requirements
Must have
• Pinned Tidy logo

```html
<!DOCTYPE html>
<html lang="en">
<head>
<meta charset="utf-8">
<title>Pinned Tidy – Jumpstart Drill School banner set</title>
<link rel="stylesheet" href="https://fonts.googleapis.com/css2?family=PT+Sans:wght@400;700&family=PT+Sans+Narrow:wght@400;700&display=swap">
<style>
  :root {
    --backdrop: #4a2a17;
    --green: #2f8f10;
    --green-light: #7cc242;
    --white: #ffffff;
    --orange-top: #ffa23a;
    --orange-bottom: #ee6a0c;
    --ink: #111111;
    --photo-a: #f1f0ea;
    --photo-b: #cfd8c4;
    --photo-c: #b9cf9a;
  }
  * { box-sizing: border-box; margin: 0; padding: 0; }
  html, body { width: 1200px; height: 800px; overflow: hidden; background: var(--backdrop); }
  .stage {
    position: relative; width: 1050px; height: 700px;
    transform: scale(1.142857); transform-origin: 0 0;
    font-family: "PT Sans", Arial, sans-serif; color: var(--white);
  }
  .banner { position: absolute; background: var(--green); overflow: hidden; }
  .banner--sky { left: 63px; top: 22px; width: 160px; height: 600px; }
  .banner--rect-a { left: 274px; top: 157px; width: 300px; height: 250px; }
  .banner--rect-b { left: 599px; top: 157px; width: 300px; height: 250px; }
  .banner--board { left: 251px; top: 438px; width: 728px; height: 90px; }

  .photo {
    position: absolute;
    background: linear-gradient(160deg, var(--photo-a) 0%, var(--photo-b) 60%, var(--photo-c) 100%);
  }
  .shape { position: absolute; left: 0; top: 0; }

  .brand-name {
    position: absolute; display: flex; align-items: center; justify-content: center;
    font-weight: 700; color: var(--green); white-space: nowrap;
  }

  .copy { position: absolute; text-align: center; }
  .headline { font-weight: 700; line-height: 1.05; }
  .headline small { font-size: 0.72em; font-weight: 700; }
  .rule { border: 0; border-top: 1px dotted rgba(255,255,255,0.7); margin: 0 auto; }
  .support { font-family: "PT Sans Narrow", "Arial Narrow", sans-serif; line-height: 1.22; }

  .cta {
    position: absolute; display: flex; align-items: center; justify-content: space-between;
    padding: 0 5px 0 16px; border-radius: 18px;
    background: linear-gradient(var(--orange-top), var(--orange-bottom));
    border: 2px solid #fbd2a4; box-shadow: 0 2px 3px rgba(0,0,0,0.35);
    font-weight: 700; color: var(--white); white-space: nowrap;
  }
  .cta .arrow { width: 24px; height: 24px; flex: none; }
</style>
</head>
<body>
<main class="stage">

  <!-- 160x600 skyscraper -->
  <section class="banner banner--sky">
    <div class="photo" style="left:0;top:78px;width:160px;height:240px" role="img" aria-label="Photo of a white wall-mounted home organising system with file pockets, notes and hooks"></div>
    <svg class="shape" width="160" height="600" viewBox="0 0 160 600" aria-hidden="true">
      <rect x="0" y="0" width="160" height="78" fill="#ffffff"/>
      <path d="M0 305 C50 290 110 290 160 300 L160 600 L0 600 Z" fill="#2f8f10"/>
      <path d="M0 305 C50 290 110 290 160 300" fill="none" stroke="#7cc242" stroke-width="4"/>
    </svg>
    <div class="brand-name" style="left:0;top:9px;width:160px;height:58px;font-size:19px">Pinned Tidy</div>
    <div class="copy" style="left:0;top:330px;width:160px">
      <p class="headline" style="font-size:20px">NOW THAT IT'S</p>
      <p class="headline" style="font-size:15px;margin-top:2px">THE <small>New</small> NEW YEAR</p>
      <hr class="rule" style="width:90px;margin-top:16px">
      <p class="headline" style="font-size:17px;margin-top:18px">IT'S TIME TO<br>GET ORGANIZED!</p>
      <hr class="rule" style="width:90px;margin-top:16px">
      <p class="support" style="font-size:13.5px;margin-top:14px">Sign Up for the Jumpstart Drill School &amp; Organize your home AND your life</p>
    </div>
    <a class="cta" style="left:8px;top:554px;width:146px;height:34px;font-size:15px">Learn More!<svg class="arrow" viewBox="0 0 24 24"><circle cx="12" cy="12" r="11" fill="#111"/><path d="M10 7l5 5-5 5" fill="none" stroke="#fff" stroke-width="2.6"/></svg></a>
  </section>

  <!-- 300x250 rectangle, two variants -->
  <section class="banner banner--rect-a">
    <div class="photo" style="left:140px;top:0;width:160px;height:250px" role="img" aria-label="Photo of a white wall-mounted home organising system with file pockets, notes and hooks"></div>
    <svg class="shape" width="300" height="250" viewBox="0 0 300 250" aria-hidden="true">
      <path d="M0 0 H208 C180 60 158 150 152 250 H0 Z" fill="#2f8f10"/>
      <path d="M208 0 C180 60 158 150 152 250" fill="none" stroke="#7cc242" stroke-width="4"/>
      <path d="M0 0 H200 C192 20 186 42 182 68 H0 Z" fill="#ffffff"/>
    </svg>
    <div class="brand-name" style="left:6px;top:6px;width:160px;height:56px;font-size:19px">Pinned Tidy</div>
    <div class="copy" style="left:0;top:80px;width:150px">
      <p class="headline" style="font-size:19px">NOW THAT IT'S</p>
      <p class="headline" style="font-size:14px;margin-top:2px">THE <small>New</small> NEW YEAR</p>
      <hr class="rule" style="width:90px;margin-top:8px">
      <p class="headline" style="font-size:16px;margin-top:8px">IT'S TIME TO<br>GET ORGANIZED!</p>
      <hr class="rule" style="width:90px;margin-top:8px">
      <p class="support" style="font-size:13px;margin-top:6px">Sign Up for the Jumpstart Drill School &amp; Organize your home AND your life</p>
    </div>
    <a class="cta" style="left:152px;top:205px;width:143px;height:33px;font-size:14px">Learn More!<svg class="arrow" viewBox="0 0 24 24"><circle cx="12" cy="12" r="11" fill="#111"/><path d="M10 7l5 5-5 5" fill="none" stroke="#fff" stroke-width="2.6"/></svg></a>
  </section>

  <section class="banner banner--rect-b">
    <div class="photo" style="left:140px;top:0;width:160px;height:250px" role="img" aria-label="Photo of a white wall-mounted home organising system with file pockets, notes and hooks"></div>
    <svg class="shape" width="300" height="250" viewBox="0 0 300 250" aria-hidden="true">
      <path d="M0 0 H208 C180 60 158 150 152 250 H0 Z" fill="#2f8f10"/>
      <path d="M208 0 C180 60 158 150 152 250" fill="none" stroke="#7cc242" stroke-width="4"/>
      <path d="M0 0 H200 C192 20 186 42 182 68 H0 Z" fill="#ffffff"/>
    </svg>
    <div class="brand-name" style="left:6px;top:6px;width:160px;height:56px;font-size:19px">Pinned Tidy</div>
    <div class="copy" style="left:0;top:80px;width:150px">
      <p class="headline" style="font-size:19px">NOW THAT IT'S</p>
      <p class="headline" style="font-size:14px;margin-top:2px">THE <small>New</small> NEW YEAR</p>
      <hr class="rule" style="width:90px;margin-top:8px">
      <p class="headline" style="font-size:16px;margin-top:8px">IT'S TIME TO<br>GET ORGANIZED!</p>
      <hr class="rule" style="width:90px;margin-top:8px">
      <p class="support" style="font-size:13px;margin-top:6px">Sign Up for the Jumpstart Drill School &amp; Organize your home AND your life</p>
    </div>
    <a class="cta" style="left:152px;top:205px;width:143px;height:33px;font-size:14px">Learn More!<svg class="arrow" viewBox="0 0 24 24"><circle cx="12" cy="12" r="11" fill="#111"/><path d="M10 7l5 5-5 5" fill="none" stroke="#fff" stroke-width="2.6"/></svg></a>
  </section>

  <!-- 728x90 leaderboard -->
  <section class="banner banner--board">
    <div class="photo" style="left:470px;top:0;width:258px;height:90px" role="img" aria-label="Photo of a white wall-mounted home organising system with file pockets, notes and hooks"></div>
    <svg class="shape" width="728" height="90" viewBox="0 0 728 90" aria-hidden="true">
      <rect x="0" y="0" width="153" height="90" fill="#ffffff"/>
      <path d="M153 0 H525 C505 30 490 60 482 90 H153 Z" fill="#2f8f10"/>
      <path d="M525 0 C505 30 490 60 482 90" fill="none" stroke="#7cc242" stroke-width="4"/>
    </svg>
    <div class="brand-name" style="left:0;top:15px;width:153px;height:60px;font-size:19px">Pinned Tidy</div>
    <div class="copy" style="left:158px;top:7px;width:320px">
      <p class="headline" style="font-size:17px">NOW THAT IT'S THE <small>New</small> NEW YEAR</p>
      <p class="headline" style="font-size:21px;margin-top:2px">IT'S TIME TO GET ORGANIZED!</p>
      <p class="support" style="font-size:13px;margin:2px auto 0;width:290px;line-height:1.15">Sign Up for the Jumpstart Drill School &amp; Organize your home AND your life</p>
    </div>
    <a class="cta" style="left:555px;top:35px;width:150px;height:33px;font-size:15px">Learn More!<svg class="arrow" viewBox="0 0 24 24"><circle cx="12" cy="12" r="11" fill="#111"/><path d="M10 7l5 5-5 5" fill="none" stroke="#fff" stroke-width="2.6"/></svg></a>
  </section>

</main>
</body>
</html>
```